graphic showing our process of education as a process called a pipeline

Also see my updated comments on discussion section.
Title of the graphic needs to be:
TITLE = The KESIMA Strategic Leadership Pipeline = larger, bold heading
SUB-TITLE = Developing a steady flow of servant leaders for Tanzania's future = under title; smaller font
change the text for each of the 7 steps to match the outcomes listed on the newly attached PDF (strategic pipeline 11x17)
Pipe should be straight or mostly straight.
Pipe should not be in a strong or dark color.
Any icons or symbols should be simple and professional, not like cartoon or childish.
We need a graphic design that shows our PROCESS, called a "pipeline," that is creating future leaders. We are a US-based non-profit that operates a Christian school in rural Tanzania for 600 students (pre-K through 12th grade). It starts with child sponsorship program that allows poor children and orphans to attend school, we have a primary school (like USA elementary school, pre-K thru 7th), and are building a secondary boarding school (like USA middle and high school, grades 8-12), where students will live on campus in dormitories. We offer education, scholarships, leadership development experiences, help finding and securing college scholarships, academic and career counseling, placements for internships and jobs, and networking and leadership development content and events to create the next generation of servant leaders for the country. Prominent colors should probably be the green, blue and black in the Tanzania flag; we want the design to communicate "smart" and "strategic." The stages of the pipeline need to be properly named; we need to show a "leak" in the pipeline after the primary school because we currently have to send our students AWAY to other boarding schools because we don't have one. As the attached recording says, this is bad for their progress. The attached pipeline graphic is very rough and NOT meant to be imitated. It is factually correct, but is busy and not attractive.

Target Market(s)

Major financial contributors and foundations that want to give money to the cause

Industry/Entity Type

non-profit/Christian ministry in education

Font styles to use
Sans Serif

Requirements
Must have
• A "smart" and strategic" feel; preferably visible when on a half page
Nice to have
• a smart, sophisticated, serious look and feel
Should not have
• an elementary school feel

```html
<!DOCTYPE html>
<html lang="en">
<head>
<meta charset="UTF-8">
<title>KESIMA Leadership Pipeline</title>
<link rel="stylesheet" href="https://fonts.googleapis.com/css2?family=Montserrat:wght@500;600;700;800&display=swap">
<style>
  :root {
    --brand-blue: #1a9fe0;
    --pipe-blue: #b5e6f8;
    --flange-blue: #86d3f1;
    --stub-green: #a6ecc6;
    --accent-green: #3dbb4c;
    --ink: #1b1b1b;
    --paper: #ffffff;
  }
  * { box-sizing: border-box; margin: 0; padding: 0; }
  html, body { width: 1200px; height: 1200px; overflow: hidden; background: var(--paper); }
  body { font-family: "Montserrat", Arial, sans-serif; color: var(--ink); position: relative; }

  .pipeline-panel { position: absolute; left: 0; width: 1200px; height: 548px; }
  .pipeline-panel--leaking { top: 0; }
  .pipeline-panel--sealed { top: 548px; }

  .pipeline-title {
    position: absolute; top: 104px; left: 0; width: 100%;
    text-align: center; font-weight: 800; font-size: 43px; letter-spacing: 0.2px;
    color: var(--brand-blue); line-height: 1;
  }
  .pipeline-subtitle {
    position: absolute; top: 158px; left: 0; width: 100%;
    text-align: center; font-weight: 600; font-size: 17px; color: var(--ink); line-height: 1.2;
  }
  .subtitle-rule { position: absolute; top: 168px; height: 2px; background: var(--accent-green); }
  .subtitle-rule--left { left: 222px; width: 68px; }
  .subtitle-rule--right { left: 922px; width: 68px; }

  .pipe-art { position: absolute; left: 0; top: 0; width: 1200px; height: 548px; }

  .stage-card { position: absolute; top: 229px; width: 104px; height: 146px; }
  .stage-header {
    height: 60px; background: var(--brand-blue); border-radius: 8px 8px 0 0;
    color: var(--paper); font-weight: 700; font-size: 8.6px; line-height: 1.2;
    text-align: center; text-transform: uppercase; padding: 9px 4px 0;
  }
  .outcome-tag {
    position: absolute; top: 51px; left: 17px; width: 70px; height: 13px;
    background: var(--accent-green); border: 1.5px solid var(--paper);
    color: var(--paper); font-weight: 800; font-size: 8px; line-height: 10px; text-align: center;
  }
  .stage-outcome {
    height: 86px; border: 1.5px dotted var(--brand-blue); border-top: none;
    border-radius: 0 0 8px 8px; background: var(--paper);
    font-weight: 500; font-size: 8.6px; line-height: 1.25; text-align: center; padding: 12px 6px 0;
  }

  .stage-icon { position: absolute; top: 530px; width: 46px; height: 46px; background: var(--ink); border-radius: 6px; }
  .pipeline-panel--sealed .stage-icon { top: 528px; }
</style>
</head>
<body>

<!-- Panel 1: pipeline with a leak after primary school -->
<section class="pipeline-panel pipeline-panel--leaking">
  <h1 class="pipeline-title">KESIMA Leadership Pipeline</h1>
  <span class="subtitle-rule subtitle-rule--left"></span>
  <p class="pipeline-subtitle">Developing a steady flow of servant leaders for Tanzania's future</p>
  <span class="subtitle-rule subtitle-rule--right"></span>

  <svg class="pipe-art" viewBox="0 0 1200 548" aria-hidden="true">
    <defs>
      <linearGradient id="stubFlowA" x1="0" y1="0" x2="0" y2="1">
        <stop offset="0" stop-color="#a6ecc6"/>
        <stop offset="1" stop-color="#b5e6f8"/>
      </linearGradient>
    </defs>
    <rect x="206" y="254" width="804" height="13" fill="var(--pipe-blue)"/>
    <g fill="var(--accent-green)">
      <rect x="256" y="251" width="4" height="19"/><rect x="288" y="251" width="4" height="19"/>
      <rect x="390" y="251" width="4" height="19"/><rect x="422" y="251" width="4" height="19"/>
      <rect x="524" y="251" width="4" height="19"/><rect x="556" y="251" width="4" height="19"/>
      <rect x="658" y="251" width="4" height="19"/><rect x="690" y="251" width="4" height="19"/>
      <rect x="791" y="251" width="4" height="19"/><rect x="823" y="251" width="4" height="19"/>
      <rect x="925" y="251" width="4" height="19"/><rect x="957" y="251" width="4" height="19"/>
    </g>
    <g>
      <rect x="192" y="391" width="28" height="42" fill="url(#stubFlowA)"/>
      <rect x="327" y="391" width="28" height="42" fill="url(#stubFlowA)"/>
      <rect x="461" y="391" width="28" height="42" fill="url(#stubFlowA)"/>
      <rect x="595" y="391" width="28" height="42" fill="url(#stubFlowA)"/>
      <rect x="729" y="391" width="28" height="42" fill="url(#stubFlowA)"/>
      <rect x="862" y="391" width="28" height="42" fill="url(#stubFlowA)"/>
      <rect x="996" y="391" width="28" height="42" fill="url(#stubFlowA)"/>
    </g>
    <g fill="var(--accent-green)">
      <rect x="188" y="385" width="36" height="6"/><rect x="323" y="385" width="36" height="6"/>
      <rect x="457" y="385" width="36" height="6"/><rect x="591" y="385" width="36" height="6"/>
      <rect x="725" y="385" width="36" height="6"/><rect x="858" y="385" width="36" height="6"/>
      <rect x="992" y="385" width="36" height="6"/>
    </g>
    <rect x="134" y="431" width="928" height="34" fill="var(--pipe-blue)"/>
    <g fill="var(--flange-blue)">
      <rect x="132" y="425" width="5" height="46"/><rect x="270" y="425" width="5" height="46"/>
      <rect x="407" y="425" width="5" height="46"/><rect x="542" y="425" width="5" height="46"/>
      <rect x="676" y="425" width="5" height="46"/><rect x="810" y="425" width="5" height="46"/>
      <rect x="944" y="425" width="5" height="46"/><rect x="1059" y="425" width="5" height="46"/>
    </g>
    <g class="pipe-leak">
      <polyline points="408,436 401,448 410,450 400,464" fill="none" stroke="var(--brand-blue)" stroke-width="2.5" stroke-linejoin="round"/>
      <path d="M404 468 C404 468 394 481 394 488 C394 494 398 498 404 498 C410 498 414 494 414 488 C414 481 404 468 404 468 Z" fill="var(--brand-blue)"/>
      <path d="M399 488 C399 492 401 494 404 494" fill="none" stroke="#ffffff" stroke-width="1.5" stroke-linecap="round"/>
    </g>
    <g stroke="var(--brand-blue)" stroke-width="1.5" stroke-dasharray="2 3">
      <line x1="206" y1="470" x2="206" y2="520"/><line x1="341" y1="470" x2="341" y2="520"/>
      <line x1="475" y1="470" x2="475" y2="520"/><line x1="609" y1="470" x2="609" y2="520"/>
      <line x1="743" y1="470" x2="743" y2="520"/><line x1="876" y1="470" x2="876" y2="520"/>
      <line x1="1010" y1="470" x2="1010" y2="520"/>
    </g>
  </svg>

  <div class="stage-card" style="left:154px"><div class="stage-header">KESIMA Sponsorship Program</div><span class="outcome-tag">OUTCOME</span><div class="stage-outcome">Establishing spiritual, academic,and health foundations</div></div>
  <div class="stage-card" style="left:289px"><div class="stage-header">KESIMA Primary School</div><span class="outcome-tag">OUTCOME</span><div class="stage-outcome">Potential leaders with Biblical worldview and strong academic foundations.</div></div>
  <div class="stage-card" style="left:423px"><div class="stage-header">KESIMA Secondary School</div><span class="outcome-tag">OUTCOME</span><div class="stage-outcome">Emerging leaders with concrete skills and strong servant mindset.</div></div>
  <div class="stage-card" style="left:557px"><div class="stage-header">KESIMA Service Leadership Experience</div><span class="outcome-tag">OUTCOME</span><div class="stage-outcome">Growing servant leaders with practical experience to effect change for the kingdom</div></div>
  <div class="stage-card" style="left:691px"><div class="stage-header">KESIMA Higher Education Support</div><span class="outcome-tag">OUTCOME</span><div class="stage-outcome">Expanding vision, capability, and motivation to solve bigger challenges for the nation.</div></div>
  <div class="stage-card" style="left:824px"><div class="stage-header">KESIMA Employment Center</div><span class="outcome-tag">OUTCOME</span><div class="stage-outcome">Capable Christ-centered leaders in the marketplace as value adding employees and entrepreneurs.</div></div>
  <div class="stage-card" style="left:958px"><div class="stage-header">KESIMA Leadership Hub</div><span class="outcome-tag">OUTCOME</span><div class="stage-outcome">Mature Christian leaders being placed and positioned for leadership roles in the community and nation.</div></div>

  <div class="stage-icon" style="left:183px" role="img" aria-label="Icon: sponsor holding a money bag"></div>
  <div class="stage-icon" style="left:318px" role="img" aria-label="Icon: two young children"></div>
  <div class="stage-icon" style="left:452px" role="img" aria-label="Icon: two teenage students"></div>
  <div class="stage-icon" style="left:586px" role="img" aria-label="Icon: group of four people"></div>
  <div class="stage-icon" style="left:720px" role="img" aria-label="Icon: graduation cap"></div>
  <div class="stage-icon" style="left:853px" role="img" aria-label="Icon: office building with employees"></div>
  <div class="stage-icon" style="left:987px" role="img" aria-label="Icon: large crowd of people"></div>
</section>

<!-- Panel 2: sealed pipeline -->
<section class="pipeline-panel pipeline-panel--sealed">
  <h1 class="pipeline-title">KESIMA Leadership Pipeline</h1>
  <span class="subtitle-rule subtitle-rule--left"></span>
  <p class="pipeline-subtitle">Developing a steady flow of servant leaders for Tanzania's future</p>
  <span class="subtitle-rule subtitle-rule--right"></span>

  <svg class="pipe-art" viewBox="0 0 1200 548" aria-hidden="true">
    <defs>
      <linearGradient id="stubFlowB" x1="0" y1="0" x2="0" y2="1">
        <stop offset="0" stop-color="#a6ecc6"/>
        <stop offset="1" stop-color="#b5e6f8"/>
      </linearGradient>
    </defs>
    <rect x="206" y="254" width="804" height="13" fill="var(--pipe-blue)"/>
    <g fill="var(--accent-green)">
      <rect x="256" y="251" width="4" height="19"/><rect x="288" y="251" width="4" height="19"/>
      <rect x="390" y="251" width="4" height="19"/><rect x="422" y="251" width="4" height="19"/>
      <rect x="524" y="251" width="4" height="19"/><rect x="556" y="251" width="4" height="19"/>
      <rect x="658" y="251" width="4" height="19"/><rect x="690" y="251" width="4" height="19"/>
      <rect x="791" y="251" width="4" height="19"/><rect x="823" y="251" width="4" height="19"/>
      <rect x="925" y="251" width="4" height="19"/><rect x="957" y="251" width="4" height="19"/>
    </g>
    <g>
      <rect x="192" y="391" width="28" height="42" fill="url(#stubFlowB)"/>
      <rect x="327" y="391" width="28" height="42" fill="url(#stubFlowB)"/>
      <rect x="461" y="391" width="28" height="42" fill="url(#stubFlowB)"/>
      <rect x="595" y="391" width="28" height="42" fill="url(#stubFlowB)"/>
      <rect x="729" y="391" width="28" height="42" fill="url(#stubFlowB)"/>
      <rect x="862" y="391" width="28" height="42" fill="url(#stubFlowB)"/>
      <rect x="996" y="391" width="28" height="42" fill="url(#stubFlowB)"/>
    </g>
    <g fill="var(--accent-green)">
      <rect x="188" y="385" width="36" height="6"/><rect x="323" y="385" width="36" height="6"/>
      <rect x="457" y="385" width="36" height="6"/><rect x="591" y="385" width="36" height="6"/>
      <rect x="725" y="385" width="36" height="6"/><rect x="858" y="385" width="36" height="6"/>
      <rect x="992" y="385" width="36" height="6"/>
    </g>
    <rect x="134" y="431" width="928" height="34" fill="var(--pipe-blue)"/>
    <g fill="var(--flange-blue)">
      <rect x="132" y="425" width="5" height="46"/><rect x="270" y="425" width="5" height="46"/>
      <rect x="407" y="425" width="5" height="46"/><rect x="542" y="425" width="5" height="46"/>
      <rect x="676" y="425" width="5" height="46"/><rect x="810" y="425" width="5" height="46"/>
      <rect x="944" y="425" width="5" height="46"/><rect x="1059" y="425" width="5" height="46"/>
    </g>
    <g stroke="var(--brand-blue)" stroke-width="1.5" stroke-dasharray="2 3">
      <line x1="206" y1="470" x2="206" y2="518"/><line x1="341" y1="470" x2="341" y2="518"/>
      <line x1="475" y1="470" x2="475" y2="518"/><line x1="609" y1="470" x2="609" y2="518"/>
      <line x1="743" y1="470" x2="743" y2="518"/><line x1="876" y1="470" x2="876" y2="518"/>
      <line x1="1010" y1="470" x2="1010" y2="518"/>
    </g>
  </svg>

  <div class="stage-card" style="left:154px"><div class="stage-header">KESIMA Sponsorship Program</div><span class="outcome-tag">OUTCOME</span><div class="stage-outcome">Establishing spiritual, academic,and health foundations</div></div>
  <div class="stage-card" style="left:289px"><div class="stage-header">KESIMA Primary School</div><span class="outcome-tag">OUTCOME</span><div class="stage-outcome">Potential leaders with Biblical worldview and strong academic foundations.</div></div>
  <div class="stage-card" style="left:423px"><div class="stage-header">KESIMA Secondary School</div><span class="outcome-tag">OUTCOME</span><div class="stage-outcome">Emerging leaders with concrete skills and strong servant mindset.</div></div>
  <div class="stage-card" style="left:557px"><div class="stage-header">KESIMA Service Leadership Experience</div><span class="outcome-tag">OUTCOME</span><div class="stage-outcome">Growing servant leaders with practical experience to effect change for the kingdom</div></div>
  <div class="stage-card" style="left:691px"><div class="stage-header">KESIMA Higher Education Support</div><span class="outcome-tag">OUTCOME</span><div class="stage-outcome">Expanding vision, capability, and motivation to solve bigger challenges for the nation.</div></div>
  <div class="stage-card" style="left:824px"><div class="stage-header">KESIMA Employment Center</div><span class="outcome-tag">OUTCOME</span><div class="stage-outcome">Capable Christ-centered leaders in the marketplace as value adding employees and entrepreneurs.</div></div>
  <div class="stage-card" style="left:958px"><div class="stage-header">KESIMA Leadership Hub</div><span class="outcome-tag">OUTCOME</span><div class="stage-outcome">Mature Christian leaders being placed and positioned for leadership roles in the community and nation.</div></div>

  <div class="stage-icon" style="left:183px" role="img" aria-label="Icon: sponsor holding a money bag"></div>
  <div class="stage-icon" style="left:318px" role="img" aria-label="Icon: two young children"></div>
  <div class="stage-icon" style="left:452px" role="img" aria-label="Icon: two teenage students"></div>
  <div class="stage-icon" style="left:586px" role="img" aria-label="Icon: group of four people"></div>
  <div class="stage-icon" style="left:720px" role="img" aria-label="Icon: graduation cap"></div>
  <div class="stage-icon" style="left:853px" role="img" aria-label="Icon: office building with employees"></div>
  <div class="stage-icon" style="left:987px" role="img" aria-label="Icon: large crowd of people"></div>
</section>

</body>
</html>
```